Brightway Haul & Upkeep Services, are a company that offers a 'one stop shop' pre-move clean up a

I have already selected a logo which I would like on the front of the business cards along with phone numbers, web address and email which are:
0487650392
www.brightwayhaul.com.au
brightwayhaulandupkeep@mailbox.example

On the back of the card I would like to list some of the types of service we offer (clean - move - repairs/maintenance) which are:
CLEAN - windows, gutters, solar panels, driveways/paths, carpets.
MOVE - Small/medium size house/office moves, large item pick-up & delivery, yard clean-up and removal.
General maintenance and repairs.

I would like the blue logo on a gray background.

Thanks

```html
<!DOCTYPE html>
<html lang="en">
<head>
<meta charset="utf-8">
<title>Brightway Haul &amp; Upkeep Services – Business Card</title>
<link rel="stylesheet" href="https://fonts.googleapis.com/css2?family=Arimo:wght@400;700&display=swap">
<style>
  :root {
    --page: #eeeeec;
    --card: #d9d9d9;
    --card-edge: #9a9a9a;
    --brand-blue: #2a6db5;
    --band-blue: #8eabc9;
    --panel-blue: #b5c5d6;
    --ink: #111111;
  }
  * { margin: 0; padding: 0; box-sizing: border-box; }
  html, body {
    width: 1200px;
    height: 1131px;
    overflow: hidden;
    background: var(--page);
    font-family: "Arimo", Arial, sans-serif;
    color: var(--ink);
  }
  .canvas { position: relative; width: 1200px; height: 1131px; }

  .card {
    position: absolute;
    width: 880px;
    height: 502px;
    background: var(--card);
    border: 1px solid var(--card-edge);
    overflow: hidden;
  }
  .card--front { left: 54px; top: 43px; }
  .card--back  { left: 278px; top: 584px; height: 501px; }

  /* Front */
  .brand-name {
    position: absolute;
    left: 38px;
    top: 128px;
    color: var(--brand-blue);
    font-weight: 700;
    text-transform: uppercase;
    line-height: 1;
  }
  .brand-name__main { display: block; font-size: 60px; letter-spacing: -0.5px; }
  .brand-name__sub  { display: block; font-size: 29px; margin-top: 16px; }

  .contact-band {
    position: absolute;
    left: 0;
    top: 300px;
    width: 100%;
    height: 154px;
    background: var(--band-blue);
  }
  .contact-list {
    position: absolute;
    left: 54px;
    top: 323px;
    list-style: none;
    font-size: 24px;
    line-height: 39px;
  }
  .contact-list li { display: flex; align-items: center; }
  .contact-list svg { width: 19px; height: 19px; margin-right: 10px; flex: none; }

  /* Back */
  .services-panel {
    position: absolute;
    left: 37px;
    top: 210px;
    width: 802px;
    height: 181px;
    background: var(--panel-blue);
    border-radius: 18px;
    text-align: center;
  }
  .services-title {
    margin-top: 20px;
    font-size: 36px;
    font-weight: 400;
    letter-spacing: 3px;
    color: var(--brand-blue);
  }
  .services-list {
    list-style: none;
    font-size: 29px;
    line-height: 40px;
    margin-top: 12px;
  }
  .services-list .dot {
    display: inline-block;
    width: 14px;
    height: 14px;
    border-radius: 50%;
    background: var(--brand-blue);
    margin: 0 14px 4px 0;
    vertical-align: middle;
  }
  .services-list .gap { margin-left: 8px; }
  .back-web {
    position: absolute;
    left: 0;
    width: 100%;
    top: 437px;
    text-align: center;
    font-size: 31px;
    letter-spacing: 3.5px;
  }
</style>
</head>
<body>
<main class="canvas">
  <section class="card card--front" aria-label="Business card front">
    <h1 class="brand-name">
      <span class="brand-name__main">Brightway Haul</span>
      <span class="brand-name__sub">&amp; Upkeep Services</span>
    </h1>
    <div class="contact-band"></div>
    <ul class="contact-list">
      <li>
        <svg viewBox="0 0 20 20" aria-hidden="true"><circle cx="10" cy="10" r="8.5" fill="none" stroke="#111" stroke-width="1.4"/><path d="M7 5.5c-1 1-1 3 1 5.5s4.5 3 5.5 2l-1.6-1.7-1.3.8c-1-.5-2-1.5-2.6-2.6l.8-1.3z" fill="#111"/></svg>
        0487650392
      </li>
      <li>
        <svg viewBox="0 0 20 20" aria-hidden="true"><g fill="none" stroke="#111" stroke-width="1.3"><circle cx="10" cy="10" r="8.5"/><ellipse cx="10" cy="10" rx="3.8" ry="8.5"/><path d="M1.5 10h17M3 5.5h14M3 14.5h14"/></g></svg>
        www.brightwayhaul.com.au
      </li>
      <li>
        <svg viewBox="0 0 20 20" aria-hidden="true"><path d="M2 8l8-5 8 5v9H2z" fill="#111"/><path d="M4 9l6 4 6-4" fill="none" stroke="#d9d9d9" stroke-width="1.4"/></svg>
        brightwayhaulandupkeep@mailbox.example
      </li>
    </ul>
  </section>

  <section class="card card--back" aria-label="Business card back">
    <div class="services-panel">
      <h2 class="services-title">Services we offer</h2>
      <ul class="services-list">
        <li><span class="dot"></span>CLEAN <span class="dot gap"></span> MOVE</li>
        <li><span class="dot"></span>GENERAL MAINTENANCE AND REPAIRS.</li>
      </ul>
    </div>
    <p class="back-web">www.brightwayhaul.com.au</p>
  </section>
</main>
</body>
</html>
```